Zelvo Stationary

Design the stationary of Zelvo Promotions Group.

Zelvo is a BTL company, BTL meaning "below the line". In other words Zelvo is a Promotional Marketing company (the company that design the brands promotional activities).

The design should transmit creativity, agility, boldness.

I need:
* Bis Card
* Letter head
* Envelopes, both vertical and horizontal (for legal size), and letter envelope
* Folders
* PPT template (Title page and regular page)
* CD slip (CD envelope)
* ID card (employee card)

And what ever else you want to throw in.
Updates

Guys,

Something I missed from the brief.   The predominat color should be RED.

Also, have fun and play with the exclamation mark (!) of the logo. 

Hi guys, more comments:

Remember that Zelvo is a "creativity" agency, not in the advertising side but on the promotional side, and that should reflect on the stationary.

 I want a bold design.  Bold and yet crisp.

 

Guys, i just uploaded the Logo in AI format.

I Also uploaded the actual Zelvo Bis Card, wich I like.  So I will like to see some designs with that bis card approach.

Guys, I am so sorry, but I notice in your last post that I upladed a wrong design ("13154_promotions_group_zelvo_brief225630.ai").  The problem was that I asked the designer the file in AI format and he send me thw wrong file, and since I dont have Illustrator I could not verify it.

The differences are minor, I just already ask him the correct one (similar to the EPS file).

Sorry                                   

Just post the correct AI file : "Zelvo Logo.ai"

Reason: I'm expecting more designs to choose from and also I wont be available tomorrow to decide.

Reason: Sorry guys, but we are not there yet!

Target Market(s)

Marketing directors, Marketing Managers

Industry/Entity Type

Legal

Requirements
Must have
• Must work with the logo attached.
The predominat color should be RED.
Play and have fun with the exclamation mark (!).
Should not have
• * No old fonts

Should not be:
* boring
* Informal
* rigid

```html
<!DOCTYPE html>
<html lang="en">
<head>
<meta charset="UTF-8">
<title>Zelvo Promotions Group – Business Card</title>
<link href="https://fonts.googleapis.com/css2?family=Jost:wght@400;500;700&display=swap" rel="stylesheet">
<style>
  :root {
    --page-bg: #ecebe8;
    --card-white: #f2f2f2;
    --card-white-edge: #e2e2e2;
    --brand-red: #c8161d;
    --brand-red-dark: #9c1016;
    --ink: #1e1e1e;
    --ink-soft: #5a5a5a;
    --white: #ffffff;
  }
  * { margin: 0; padding: 0; box-sizing: border-box; }
  html, body { width: 1200px; height: 900px; overflow: hidden; }
  body {
    background: var(--page-bg);
    font-family: "Jost", "Futura", sans-serif;
    display: flex;
    align-items: center;
    justify-content: center;
    gap: 120px;
  }
  .card {
    width: 340px;
    height: 580px;
    border-radius: 22px;
    position: relative;
    box-shadow: 0 10px 28px rgba(0,0,0,0.18);
  }

  /* Front */
  .card-front {
    background: linear-gradient(160deg, var(--white) 0%, var(--card-white) 55%, var(--card-white-edge) 100%);
    color: var(--ink);
  }
  .brand {
    position: absolute;
    top: 46px;
    right: 42px;
    display: flex;
    align-items: center;
    gap: 10px;
  }
  .brand-name {
    font-weight: 700;
    font-size: 44px;
    letter-spacing: -0.5px;
    color: #2b2b2b;
    line-height: 1;
  }
  .brand-dot {
    width: 18px; height: 18px;
    border-radius: 50%;
    background: var(--brand-red);
  }
  .person {
    position: absolute;
    top: 262px;
    left: 0; right: 0;
    text-align: center;
  }
  .person-name {
    color: var(--brand-red);
    font-weight: 700;
    font-size: 22px;
  }
  .person-role {
    color: var(--ink-soft);
    font-size: 17px;
    margin-top: 2px;
  }
  .address {
    position: absolute;
    top: 362px;
    left: 0; right: 0;
    text-align: center;
    font-size: 18px;
    font-weight: 500;
    line-height: 1.3;
  }
  .contact {
    position: absolute;
    top: 448px;
    left: 58px;
    list-style: none;
    font-size: 18px;
    line-height: 1.28;
  }
  .contact-key {
    color: var(--brand-red);
    font-weight: 700;
    display: inline-block;
    width: 16px;
  }

  /* Back */
  .card-back {
    background: linear-gradient(155deg, var(--brand-red) 0%, #b8141a 55%, var(--brand-red-dark) 100%);
    color: var(--white);
  }
  .back-brand {
    position: absolute;
    top: 220px;
    left: 0; right: 0;
    display: flex;
    align-items: center;
    justify-content: center;
    gap: 12px;
  }
  .back-brand .brand-name { color: var(--white); font-size: 56px; }
  .back-brand .brand-dot { background: var(--white); width: 22px; height: 22px; }
  .web {
    position: absolute;
    bottom: 44px;
    left: 0; right: 0;
    text-align: center;
    font-size: 18px;
    letter-spacing: 0.5px;
  }
</style>
</head>
<body>
  <section class="card card-front" aria-label="Business card front">
    <div class="brand">
      <span class="brand-name">zelvo</span>
      <span class="brand-dot"></span>
    </div>
    <div class="person">
      <p class="person-name">Your Name</p>
      <p class="person-role">Position</p>
    </div>
    <p class="address">123, Your Street,<br>Your City, Country, 123.</p>
    <ul class="contact">
      <li><span class="contact-key">P</span> (123) 456 7890</li>
      <li><span class="contact-key">F</span> (123) 456 7890</li>
      <li><span class="contact-key">E</span> info@zelvo.com</li>
    </ul>
  </section>

  <section class="card card-back" aria-label="Business card back">
    <div class="back-brand">
      <span class="brand-name">zelvo</span>
      <span class="brand-dot"></span>
    </div>
    <p class="web">www.Zelvo.com</p>
  </section>
</body>
</html>
```